VELORA SPORTS NETWORK

design a website that will be a companion to a sports network that features womens sports and fitness content.
With the goal of promoting and empowering female athleticism, Velorabx.example will be the online network that connects female sports fans to the sports they love and follow. The site aims to raise the level of awareness of women in sports by providing comprehensive sports coverage, spotlighting outstanding achievements, and working with sporting associations on advocacy issues and empowering programs.
Updates
I would like to have all entry by Sunday June 8 2014 thank you
please use actual script not lorem ipsum
thank you
Deadline winding down, added new pictures to file
Target Market(s)
our target market is females 18-54, whom love womens sports and ftiness
Industry/Entity Type
Fitness
Font styles to use
Requirements
Must have
- Attributes of the website:
1. Large Photos: to accompany current stories
2. Colorful: Highlight Velora’s officials colors
3. News Area: recent news items on the home page and achieved news stories
4. Featured Content area: Headline news, athlete spotlights and issues
5. Streaming content: to accompany news and featured content
6. Advertiser links: to purchase merchandise
7. Real-time scores of live events
8. Blog
9. Monthly newsletter
10. Athlete profile page
11. Model close to KVRM
Nice to have
- Velorabx.example will offer value-added service that will entitle customers to gain access to online streaming services provided by Velora, which delivers both live streams and on-demand replays of global women’s sports events to sports fans in U.S. and abroad. This service will be subscription based for a modest monthly fee. Content will be available across multiple platforms and cloud based. New subscriber will get first 30 days free.
Content will include:
1. Live sports events
2. On-demand and premium content
3. Fan-generated Content

```html
<!DOCTYPE html>
<html lang="en">
<head>
<meta charset="utf-8">
<title>Velora Sports Network</title>
<link rel="stylesheet" href="https://fonts.googleapis.com/css2?family=Open+Sans:wght@400;600;700&display=swap">
<style>
:root{
  --orange:#e9582b;
  --orange-dark:#c9431b;
  --red:#b8141c;
  --red-bright:#d3212a;
  --text:#333;
  --muted:#777;
  --line:#dcdcdc;
  --footer:#222;
  --footer-band:#333;
  --white:#fff;
}
*{box-sizing:border-box;margin:0;padding:0}
html,body{width:1200px;height:2353px;overflow:hidden}
body{position:relative;background:var(--white);font-family:"Open Sans",Arial,sans-serif;color:var(--text)}
.abs{position:absolute}

/* hero */
.hero{left:0;top:0;width:1200px;height:700px;background:radial-gradient(ellipse at 42% 45%,#8fa47a 0%,#4f7a32 35%,#274d16 70%,#12260a 100%)}
.brand{left:99px;top:0;width:130px;height:166px;background:var(--white);display:flex;flex-direction:column;align-items:center;justify-content:center;gap:8px}
.brand-mark{width:46px;height:46px;border-radius:50%;background:var(--orange)}
.brand-name{color:var(--orange);font-weight:700;font-size:16px;text-align:center;line-height:1.2}
.nav{left:229px;top:0;width:872px;height:50px;background:var(--orange);display:flex;align-items:stretch}
.nav a{color:var(--white);text-decoration:none;font-size:14px;font-weight:600;padding:0 17px;display:flex;align-items:center;border-right:1px solid rgba(0,0,0,.12);text-transform:uppercase}
.nav a.active{background:var(--orange-dark)}
.nav .social{margin-left:auto;display:flex;align-items:center;gap:6px;padding-right:18px}
.social-box{width:24px;height:24px;border-radius:3px;background:var(--white)}
.caption{left:685px;top:212px;width:416px;height:278px;background:rgba(30,30,30,.78);padding:18px 18px;color:var(--white)}
.caption .kicker{font-size:21px;font-weight:600}
.caption h1{font-size:30px;font-weight:700;line-height:1.25;margin-top:6px;text-transform:uppercase}
.caption p{font-size:13px;line-height:1.7;color:#ddd;margin-top:14px}
.caption .btn{display:inline-block;margin-top:16px;background:var(--white);color:var(--red-bright);font-size:14px;padding:6px 11px;border-radius:2px}
.slider-arrows{left:1046px;top:507px;display:flex;gap:2px}
.slider-arrows span{width:24px;height:24px;border-radius:50%;background:var(--white);display:flex;align-items:center;justify-content:center}

/* intro */
.intro{left:140px;top:735px;width:920px;text-align:center;font-size:15px;line-height:1.78;color:var(--muted)}
.rule{height:1px;background:var(--line)}

/* sections */
.section-title{font-size:24px;font-weight:600;color:var(--red)}
.section-next{width:17px;height:17px;border-radius:50%;background:#bdbdbd;display:flex;align-items:center;justify-content:center}
.card{width:231px}
.card .thumb{width:231px;height:145px}
.card h3{font-size:16px;font-weight:600;color:var(--orange);margin-top:8px;padding-left:3px}
.card time{display:block;font-size:13px;padding-left:3px;margin-top:2px}
.card p{font-size:11.5px;line-height:1.55;color:var(--muted);padding-left:3px;margin-top:10px}
.btn-more{display:inline-block;margin:11px 0 0 3px;background:var(--orange);color:var(--white);font-size:12px;padding:4px 9px}

/* blog */
.post{left:99px;width:740px;height:170px;border:1px solid var(--line);display:flex}
.post .thumb{width:166px;height:168px;flex:none}
.post .body{padding:22px 24px}
.post h3{font-size:17px;font-weight:400;color:#444}
.post p{font-size:12px;line-height:1.6;color:#999;margin-top:8px}
.post .meta{display:flex;gap:22px;align-items:center;font-size:12px;color:#999;margin-top:12px}

/* sidebar */
.newsletter{left:860px;top:930px;width:241px;height:146px;background:var(--red-bright);padding:14px 16px;color:var(--white)}
.newsletter h2{font-size:21px;font-weight:600}
.newsletter p{font-size:11.5px;line-height:1.5;margin-top:6px}
.newsletter .field{margin-top:12px;height:34px;background:var(--white);display:flex;align-items:center;justify-content:space-between;padding:0 6px 0 12px;color:#999;font-size:12px}
.video{left:860px;width:239px}
.video .thumb{width:239px;height:146px;display:flex;align-items:center;justify-content:center}
.video h3{font-size:16px;font-weight:600;color:var(--orange);margin-top:9px;padding-left:3px}
.video time{display:block;font-size:13px;padding-left:3px;margin-top:2px}

/* scores */
.scores{left:0;top:2147px;width:1200px;height:60px;background:var(--footer-band)}
.scores-label{left:99px;top:2147px;width:111px;height:60px;background:var(--orange);color:var(--white);font-size:14px;line-height:1.25;padding:12px 14px;display:flex;align-items:center;justify-content:space-between}
.score-cell{top:2147px;width:104px;height:60px;border-left:1px solid #555;padding:10px 14px;font-size:13px;color:#ddd;line-height:1.5}
.score-cell b{color:var(--orange);font-weight:600;margin-left:12px}
.score-cell.alt{color:#999}
.scores-all{left:941px;top:2147px;width:160px;height:60px;background:var(--orange);color:var(--white);font-size:14px;display:flex;align-items:center;justify-content:center}
.footer{left:0;top:2207px;width:1200px;height:146px;background:var(--footer)}
.footer-nav{left:99px;top:2232px;width:1002px;display:flex;justify-content:space-around;font-size:13px;color:#bbb}
.footer-nav span::before{content:"• ";color:#888}
.footer-rule{left:99px;top:2276px;width:1002px;height:1px;background:#3a3a3a}
.copyright{left:101px;top:2303px;font-size:13px;color:#bbb}
.footer-social{left:1003px;top:2301px;display:flex;gap:6px}
</style>
</head>
<body>

<div class="abs hero" role="img" aria-label="Football hitting the back of a goal net on a green pitch"></div>
<div class="abs brand"><span class="brand-mark"></span><span class="brand-name">VELORA<br>SPORTS NETWORK</span></div>
<nav class="abs nav">
  <a class="active">Home</a><a>About us</a><a>News</a><a>Live Events</a><a>Blog</a><a>Sports</a><a>Register / Login</a>
  <span class="social"><span class="social-box"></span><span class="social-box"></span><span class="social-box"></span></span>
</nav>
<div class="abs caption">
  <div class="kicker">Phasellus fringilla miquis</div>
  <h1>Donec porttitor erat volutpat hendrer</h1>
  <p>Curabitur porta lectus ac ultricies aliquam. Morbi ullamcor per nisi arcu, sed aliquam tellus porta ut. Integer ultrices lectus quam, et mattis erat volutpat ac.</p>
  <span class="btn">Read more</span>
</div>
<div class="abs slider-arrows">
  <span><svg width="10" height="10"><path d="M7 1 L2 5 L7 9Z" fill="#333"/></svg></span>
  <span><svg width="10" height="10"><path d="M3 1 L8 5 L3 9Z" fill="#333"/></svg></span>
</div>

<p class="abs intro">Velorabx.example will offer value-added service that will entitle customers to gain access to online streaming services provided by Velora, which delivers both live streams and on-demand replays of global women’s sports events to sports fans in U.S. and abroad. This service will be subscription based for a modest monthly fee. Content will be available across multiple platforms and cloud based. New subscriber will get first 30 days free.</p>
<div class="abs rule" style="left:99px;top:886px;width:1002px"></div>

<!-- Latest News -->
<h2 class="abs section-title" style="left:99px;top:920px">Latest News</h2>
<span class="abs section-next" style="left:820px;top:930px"><svg width="7" height="8"><path d="M1 0 L6 4 L1 8Z" fill="#fff"/></svg></span>
<article class="abs card" style="left:102px;top:974px"><div class="thumb" role="img" aria-label="Footballer striking a ball under a stormy sky" style="background:linear-gradient(160deg,#8c7a4e,#c9a85c 45%,#4a3d22)"></div><h3>Aenean aliquam malesuada</h3><time>June 1, 2014</time><p>Etiam non varius ipsum. Praesent et ligula id orci elementum imperdiet sit amet at augue. Morbi mi massa, fauci­bus eu eleifend eget, volutpat.</p><span class="btn-more">View more</span></article>
<article class="abs card" style="left:356px;top:974px"><div class="thumb" role="img" aria-label="Women's lacrosse players on a green field" style="background:linear-gradient(180deg,#6d8a5a,#3f6b33 60%,#2e5a28)"></div><h3>Aenean aliquam malesuada</h3><time>June 1, 2014</time><p>Etiam non varius ipsum. Praesent et ligula id orci elementum imperdiet sit amet at augue. Morbi mi massa, fauci­bus eu eleifend eget, volutpat.</p><span class="btn-more">View more</span></article>
<article class="abs card" style="left:609px;top:974px"><div class="thumb" role="img" aria-label="Basketball dropping through a hoop in a dark arena" style="background:radial-gradient(circle at 60% 40%,#7a5a3a,#2a2420 55%,#111)"></div><h3>Aenean aliquam malesuada</h3><time>June 1, 2014</time><p>Etiam non varius ipsum. Praesent et ligula id orci elementum imperdiet sit amet at augue. Morbi mi massa, fauci­bus eu eleifend eget, volutpat.</p><span class="btn-more">View more</span></article>
<div class="abs rule" style="left:99px;top:1320px;width:740px"></div>

<!-- Featured News -->
<h2 class="abs section-title" style="left:99px;top:1343px">Featured News</h2>
<span class="abs section-next" style="left:820px;top:1353px"><svg width="7" height="8"><path d="M1 0 L6 4 L1 8Z" fill="#fff"/></svg></span>
<article class="abs card" style="left:102px;top:1396px"><div class="thumb" role="img" aria-label="Sprinters crouched at the starting line on a track" style="background:linear-gradient(180deg,#8a6a55,#b5826a 55%,#a0523a)"></div><h3>Aenean aliquam malesuada</h3><time>June 1, 2014</time><span class="btn-more">View more</span></article>
<article class="abs card" style="left:356px;top:1396px"><div class="thumb" role="img" aria-label="Swimmer doing butterfly stroke in a blue pool" style="background:linear-gradient(180deg,#4fa8d8,#2b86c2 60%,#1d6ea8)"></div><h3>Aenean aliquam malesuada</h3><time>June 1, 2014</time><span class="btn-more">View more</span></article>
<article class="abs card" style="left:609px;top:1396px"><div class="thumb" role="img" aria-label="Hurdler clearing a hurdle in a stadium" style="background:linear-gradient(180deg,#8b9aa8,#7c8a6e 55%,#9a5a40)"></div><h3>Aenean aliquam malesuada</h3><time>June 1, 2014</time><span class="btn-more">View more</span></article>
<div class="abs rule" style="left:99px;top:1667px;width:740px"></div>

<!-- Latest Blog -->
<h2 class="abs section-title" style="left:99px;top:1697px">Latest Blog</h2>
<span class="abs section-next" style="left:820px;top:1705px"><svg width="7" height="8"><path d="M1 0 L6 4 L1 8Z" fill="#fff"/></svg></span>
<article class="abs post" style="top:1747px">
  <div class="thumb" role="img" aria-label="Tennis players at the net on a clay court" style="background:linear-gradient(160deg,#d9c6b4,#b4503a 55%,#7a2a1e)"></div>
  <div class="body"><h3>Fusce a magna eget lacus ultricies iaculis et vel turpis.</h3><p>Curabitur porta lectus ac ultricies aliquam. Morbi ullamcorper nisi arcu, sed aliquam tellus porta ut. Integer ultrices lectus quam, et mattis erat volutpat ac. Duis tristique dignissim posuere ultrices suscipit tempus.</p>
  <div class="meta"><span>June 2, 2014</span><svg width="14" height="12"><path d="M1 3h3l5 6h3M1 9h3l5-6h3" stroke="#999" fill="none" stroke-width="1.4"/></svg><svg width="12" height="11"><path d="M1 1h10v7H5L2 10V8H1z" fill="#999"/></svg></div></div>
</article>
<article class="abs post" style="top:1937px">
  <div class="thumb" role="img" aria-label="Young hockey player skating on ice" style="background:linear-gradient(180deg,#eef1f4,#d6dde4 60%,#c4ccd4)"></div>
  <div class="body"><h3>Fusce a magna eget lacus ultricies iaculis et vel turpis.</h3><p>Curabitur porta lectus ac ultricies aliquam. Morbi ullamcorper nisi arcu, sed aliquam tellus porta ut. Integer ultrices lectus quam, et mattis erat volutpat ac. Duis tristique dignissim posuere ultrices suscipit tempus.</p>
  <div class="meta"><span>June 2, 2014</span><svg width="14" height="12"><path d="M1 3h3l5 6h3M1 9h3l5-6h3" stroke="#999" fill="none" stroke-width="1.4"/></svg><svg width="12" height="11"><path d="M1 1h10v7H5L2 10V8H1z" fill="#999"/></svg></div></div>
</article>

<!-- Sidebar -->
<aside class="abs newsletter">
  <h2>NewsLetter Signup</h2>
  <p>Duis accumsan tortor in nibh condimentum, vitae tempor eros.</p>
  <div class="field"><span>E-mail ID</span><svg width="14" height="18"><path d="M3 2 L11 9 L3 16" stroke="#d3212a" stroke-width="3.5" fill="none"/></svg></div>
</aside>
<div class="abs" role="img" aria-label="Running shoes advertisement banner" style="left:860px;top:1093px;width:241px;height:290px;background:linear-gradient(180deg,#f1eee9 0%,#e2ddd6 68%,#0f2a3a 68%,#0b1e2a 100%)"></div>
<h2 class="abs section-title" style="left:860px;top:1402px">Latest Video</h2>
<article class="abs video" style="top:1446px"><div class="thumb" role="img" aria-label="Cheering fans in a stadium crowd" style="background:linear-gradient(160deg,#8a3a2e,#b94a36 50%,#5a1e18)"><svg width="44" height="44"><circle cx="22" cy="22" r="20" fill="#fff" stroke="#333" stroke-width="3"/><path d="M17 12 L31 22 L17 32Z" fill="#333"/></svg></div><h3>Aenean aliquam malesuada</h3><time>June 1, 2014</time></article>
<article class="abs video" style="top:1666px"><div class="thumb" role="img" aria-label="Wide view of a packed football stadium" style="background:linear-gradient(180deg,#1e2a40,#2e4a6a 50%,#3a6a3a)"><svg width="44" height="44"><circle cx="22" cy="22" r="20" fill="#fff" stroke="#333" stroke-width="3"/><path d="M17 12 L31 22 L17 32Z" fill="#333"/></svg></div><h3>Aenean aliquam malesuada</h3><time>June 1, 2014</time></article>
<article class="abs video" style="top:1885px"><div class="thumb" role="img" aria-label="Basketball player going up for a dunk" style="background:linear-gradient(160deg,#2a2540,#4a3a6a 50%,#b88a3a)"><svg width="44" height="44"><circle cx="22" cy="22" r="20" fill="#fff" stroke="#333" stroke-width="3"/><path d="M17 12 L31 22 L17 32Z" fill="#333"/></svg></div><h3>Aenean aliquam malesuada</h3><time>June 1, 2014</time></article>

<!-- Scores -->
<div class="abs scores"></div>
<div class="abs scores-label"><span>PBL<br>Scores</span><svg width="18" height="18"><circle cx="9" cy="9" r="8" fill="#b63e16"/><path d="M5 7 L9 11 L13 7" stroke="#fff" stroke-width="2" fill="none"/></svg></div>
<div class="abs score-cell" style="left:210px">GHB «<b>5</b><br>GHB «<b>5</b></div>
<div class="abs score-cell alt" style="left:314px">GHB «<b>5</b><br>GHB «<b>5</b></div>
<div class="abs score-cell" style="left:418px">GHB «<b>5</b><br>GHB «<b>5</b></div>
<div class="abs score-cell alt" style="left:522px">GHB «<b>5</b><br>GHB «<b>5</b></div>
<div class="abs score-cell" style="left:626px">GHB «<b>5</b><br>GHB «<b>5</b></div>
<div class="abs score-cell alt" style="left:730px">GHB «<b>5</b><br>GHB «<b>5</b></div>
<div class="abs score-cell" style="left:834px">GHB «<b>5</b><br>GHB «<b>5</b></div>
<div class="abs scores-all">View All PBL Scores</div>

<!-- Footer -->
<footer class="abs footer"></footer>
<nav class="abs footer-nav"><span>Home</span><span>About us</span><span>News</span><span>Live Events</span><span>Blog</span><span>Sports</span><span>Register</span><span>Login</span></nav>
<div class="abs footer-rule"></div>
<p class="abs copyright">Copyright © 2014 Velora tv.&nbsp;&nbsp;All rights reserved.</p>
<div class="abs footer-social"><span class="social-box"></span><span class="social-box"></span><span class="social-box"></span></div>

</body>
</html>
```